Calder Aviation website

We are an aviation company based in Miramar, FL but with worldwide coverage. We are involved in commercial aircraft (mostly freighters) trading, sale & leasing. Specifically, we specialized in freighters of the Veltram family (V316, V328, V335, V342, V359). We also assist with financing, sale/leaseback. Handle special aviation projects and provide consultancy services. Currently engaged in a Veltram 359 passenger to Freighter conversion (P2F).

Website Preliminary Initial Content/Sections as follows:

About Us
Founded in 2011, Calder Aviation's management has many years of experience in Aviation, a strong background in scheduled airlines with emphasis in all cargo operations, freight forwarding supply chain and freight logistics, as well as ACMI and CMI operations.

Calder’s focuses in facilitating wet and dry lease operations, charter and ACMI programs consultancy, aircraft sales, leasing and procurement, aviation consultancy and aircraft management.

Calder team is a hands-on reliable alternative that works toward achieving your aircraft and aviation objectives by meeting your requirements and timeframe throughout professional and personalized service.

Tiberio Salcedo has over three decades of experience in the aviation field including aircraft maintenance, airline management, supply chain and logistics management. Tiberio is a true entrepreneur with proven experience and expertise on the multiple facets of the commercial aviation industry throughout the creation and development of a cluster of aviation entities. Tiberio is the founder and former sole member/chairman of 64 Air, a Veltram 342 All-Cargo U.S. Certificated Air Carrier created from scratch in 2014 which nowadays conforms a superb growing airline platform with an immaculate compliance operational record.

Services

Aircraft Finance, Trading, Procurement and Leasing
Calder buys, sells, leases and facilitates aircraft trading while specializes in structured aircraft investment projects. Calder has deep industry relationships and years of expertise, allowing to successfully execute lease transactions. We assist airlines, financial institutions and leasing companies when selling or purchasing aircraft.

Aircraft Available for Sale/Lease

Sale/Leaseback
Sale-leaseback is a method of financing. If your company needs liquidity, your aircraft or engine can serve as collateral for a loan throughout a sale-leaseback transaction. Sale-leaseback can free the equity tied up in aircraft or asset. Even if there is no pressing need for funds, a sale-leaseback allows you to use the equity tied up in your aircraft in a more productive fashion. Leaseback arrangements are usually employed because they confer financing, accounting or taxation benefits.

Passenger to Freighter Conversion (P2F)
Pandemic has seen the resurgence of operators packing freight into the main cabins of passenger aircraft. Carriers have been allowed to transport cargo in the cabin by removing passenger seats completely. NAB/CARO have established exemptions that allow operators to fly in “Preighter” configuration for a limited time. Calder is closely working with a U.S. group that is developing a Class E Supplemental Type Certificate (STC) for applicability on V359 aircraft which will include a cargo door for containerized freight. Final approvals are expected during first quarter of 2022.
Wet lease
Throughout our deep relationships within the industry, Calder facilitates short or long-term wet leases to airlines and qualified parties around the globe, whereby we provide the Aircraft, Crews, Maintenance and Insurance (ACMI) worldwide services at competitive rates. We also specialize in AM leases where the aircraft is registered onto Lessee´s AOC with all maintenance services included in the rates, covering all maintenance risks, or CM or CMI where the client provides the aircraft.

Dry Lease
We offer aircraft from our own portfolio on dry lease or could engage in procuring the aircraft of your choice.

Asset & Aircraft Management
We provide aircraft owners Aircraft Management services, where we manage the technical side of the aircraft or the asset. Calder also provides Harlow Dynamics engines trading, repair and full management services. We also buy Veltram/Skylane surplus inventory.

Worldwide Charters
We facilitate the arrangement of full charters to airlines and logistics companies. Certain territory restrictions may apply.

Aviation Consultancy
We provide airline consultancy services for new or special projects. Calder also specializes on All Cargo International route analysis, implementation and development. Our team provides professional guidance in obtaining worldwide both scheduled and charter authority.

Target Market(s)

Our target market are the airlines, logistics companies and commercial aviation related entities

Industry/Entity Type

Commercial Aviation

Coding

Coded - Design and coding required

Number of Pages Required

3 page

Requirements
Must have
• Illustrations of wide body freighters such V359, V342, V328

```html
<!DOCTYPE html>
<html lang="en">
<head>
<meta charset="utf-8">
<title>Calder Aviation</title>
<link rel="stylesheet" href="https://fonts.googleapis.com/css2?family=Lora:wght@600;700&family=Nunito+Sans:wght@400;600;700;800&display=swap">
<style>
  :root{
    --navy:#111a4d;
    --navy-deep:#0b1233;
    --ink:#1d1d1f;
    --body:#4a4a4a;
    --muted:#8a8fa3;
    --soft:#f2f2f2;
    --white:#ffffff;
    --tile:#e4e5e9;
  }
  *{box-sizing:border-box;margin:0;padding:0}
  html,body{width:1200px;height:3552px;overflow:hidden;background:var(--white)}
  body{font-family:"Nunito Sans",Arial,sans-serif;color:var(--body)}
  .page{position:relative;width:1200px;height:3552px;overflow:hidden}
  .abs{position:absolute}
  .serif{font-family:"Lora",Georgia,serif}

  /* header */
  .nav a{position:absolute;top:34px;font-size:15px;font-weight:600;color:var(--navy);text-decoration:none;letter-spacing:.3px}
  .nav a.active{font-weight:800}
  .nav a.active::after{content:"";position:absolute;left:0;right:0;bottom:-7px;height:2px;background:var(--navy)}
  .brand{position:absolute;left:455px;top:0;width:290px;height:86px;text-align:center;color:var(--white);font-family:"Nunito Sans",sans-serif;font-weight:400;font-size:17px;letter-spacing:6px;line-height:24px;padding-top:16px}

  .hero-title{left:0;width:1200px;top:236px;text-align:center;font-size:57px;font-weight:700;color:var(--navy);letter-spacing:.5px}
  .hero-sub{left:0;width:1200px;top:310px;text-align:center;font-size:20px;font-weight:600;color:#1c1c2a;line-height:30px}
  .btn-solid{left:529px;top:390px;width:141px;height:48px;background:var(--navy);color:var(--white);font-size:13px;font-weight:800;text-align:center;line-height:48px;letter-spacing:.3px}

  h2.section{position:absolute;left:0;width:1200px;text-align:center;font-family:"Lora",Georgia,serif;font-weight:700;color:var(--ink);font-size:43px;letter-spacing:.5px}

  /* service cards */
  .svc{position:absolute;top:903px;width:310px;height:432px}
  .svc .shot{position:absolute;left:7px;top:0;width:296px;height:193px}
  .svc h3{position:absolute;top:1124px}
  .svc-title{position:absolute;left:0;width:310px;top:222px;text-align:center;font-size:17px;font-weight:800;color:var(--ink);letter-spacing:.3px}
  .svc-text{position:absolute;left:12px;width:286px;top:256px;text-align:center;font-size:14.5px;line-height:24px;color:var(--body)}

  /* about */
  .about-art{left:0;top:1434px;width:650px;height:472px;background:linear-gradient(100deg,#7fb6e0 0%,#9cc8ea 55%,#d6e7f3 100%)}
  .about-panel{left:600px;top:1434px;width:600px;height:472px;background:linear-gradient(90deg,rgba(242,242,242,0) 0%,var(--soft) 10%)}
  .about-title{left:659px;top:1474px;font-size:38px;font-weight:700;color:var(--ink)}
  .about-text{left:659px;width:430px;font-size:14.6px;line-height:25.6px;text-align:justify;color:#444}
  .btn-line{left:659px;top:1806px;width:141px;height:50px;border:3px solid var(--navy);color:var(--navy);font-size:13.5px;font-weight:800;text-align:center;line-height:44px}

  /* aircraft */
  .fleet{left:0;top:1906px;width:1200px;height:591px;background:linear-gradient(180deg,#0f1745,#0c1440)}
  .fleet-title{left:0;width:1200px;top:1970px;text-align:center;color:var(--white);font-size:34px;font-weight:700;line-height:41px}
  .offer{position:absolute;top:2104px;width:231px;height:317px;background:var(--white)}
  .offer .icon{position:absolute;left:79px;top:46px;width:72px;height:72px}
  .offer-title{position:absolute;left:0;width:231px;top:157px;text-align:center;font-size:15px;font-weight:800;color:var(--ink)}
  .offer-text{position:absolute;left:6px;width:219px;top:190px;text-align:center;font-size:14.2px;line-height:24px;color:var(--body)}
  .more{font-size:13.5px;font-weight:800;color:var(--navy);letter-spacing:.2px}
  .offer .more{position:absolute;left:0;width:231px;top:278px;text-align:center}

  /* blog */
  .post-img{position:absolute;top:2671px;width:311px;height:215px}
  .post{position:absolute;top:2865px;width:291px;height:187px;background:var(--white);box-shadow:0 2px 10px rgba(0,0,0,.12);text-align:center}
  .post-date{position:absolute;top:26px;left:0;width:291px;font-size:13px;color:#444}
  .post-title{position:absolute;top:57px;left:0;width:291px;font-size:15.5px;font-weight:800;color:var(--ink)}
  .post-text{position:absolute;top:87px;left:6px;width:279px;font-size:14px;line-height:22px;color:var(--body)}
  .post .more{position:absolute;top:144px;left:0;width:291px}

  /* footer */
  .foot-brand{left:112px;top:3320px;width:240px;text-align:center;color:var(--white);font-size:26px;font-weight:400;letter-spacing:6px;line-height:34px}
  .social{top:3403px;width:26px;height:26px;border:1.5px solid var(--white);border-radius:50%}
  .foot-col h4{position:absolute;font-size:19px;font-weight:800;color:var(--white)}
  .foot-list{position:absolute;list-style:none;font-size:14.5px;color:#dfe2ee;line-height:25px}
  .foot-list li::before{content:"»";margin-right:14px;font-weight:700}
  .contact-row{position:absolute;left:859px;font-size:14.5px;color:#dfe2ee;line-height:24px}
  .contact-row svg{position:absolute;left:0;top:5px}
  .contact-row span{position:absolute;left:38px;white-space:nowrap}
  .rule{left:112px;top:3494px;width:977px;height:1px;background:rgba(255,255,255,.35)}
  .copy{left:0;top:3512px;width:1200px;text-align:center;font-size:13.5px;color:#dfe2ee}
</style>
</head>
<body>
<div class="page">

  <!-- hero -->
  <svg class="abs" style="left:0;top:0" width="1200" height="720" viewBox="0 0 1200 720">
    <defs>
      <linearGradient id="heroSky" x1="0" y1="0" x2="0" y2="1">
        <stop offset="0" stop-color="#b5b8c8"/>
        <stop offset=".45" stop-color="#d9d9df"/>
        <stop offset=".72" stop-color="#c9c9cc"/>
        <stop offset="1" stop-color="#7a7b7e"/>
      </linearGradient>
    </defs>
    <polygon points="0,540 600,672 1200,540 1200,566 600,708 0,566" fill="#0f1745"/>
    <polygon points="0,0 1200,0 1200,540 600,660 0,540" fill="url(#heroSky)" role="img" aria-label="Photograph of a wide-body passenger jet on an airport apron"/>
    <g transform="translate(600,693)">
      <rect x="-17" y="-17" width="34" height="34" transform="rotate(45)" fill="#0f1745"/>
      <path d="M0,-16 L3,-3 L16,0 L3,3 L0,16 L-3,3 L-16,0 L-3,-3 Z" fill="#ffffff"/>
    </g>
    <polygon points="455,0 745,0 715,86 485,86" fill="#0f1745"/>
  </svg>
  <div class="brand">CALDER<br>AVIATION</div>
  <nav class="nav">
    <a class="active" style="left:110px">HOME</a>
    <a style="left:191px">ABOUT US</a>
    <a style="left:299px">SERVICES</a>
    <a style="left:795px">PROJECTS</a>
    <a style="left:911px">BLOG</a>
    <a style="left:987px">CONTACT US</a>
  </nav>
  <h1 class="abs hero-title serif">CALDER AVIATION</h1>
  <p class="abs hero-sub">Tiberio Salcedo has over three decades of experience in the aviation field<br>including aircraft maintenance</p>
  <div class="abs btn-solid">GET STARTED</div>

  <!-- services -->
  <h2 class="section" style="top:798px">SERVICES OFFERED</h2>

  <div class="svc" style="left:111px">
    <svg class="abs" style="left:0;top:0" width="310" height="432"><polygon points="0,0 310,0 310,360 155,413 0,360" fill="#fff" stroke="#e3e3e6"/><polyline points="0,362 155,415 310,362" fill="none" stroke="#0f1745" stroke-width="4"/><rect x="137" y="386" width="36" height="36" transform="rotate(45 155 404)" fill="#0f1745"/><path d="M155,396 V412 M147,404 H163" stroke="#fff" stroke-width="4"/></svg>
    <div class="shot" role="img" aria-label="Photograph of a businessman on the phone beside an airport window with a jet" style="background:linear-gradient(120deg,#c9d6e4,#8ea3bb 60%,#3d4655)"></div>
    <div class="svc-title">AIRCRAFT FINANCE</div>
    <p class="svc-text">Unde omnis iste natus error sit volupta tem accusantium doloremque lauda ntium, totam aperiaco nsequuntur magnimea.</p>
  </div>
  <div class="svc" style="left:445px">
    <svg class="abs" style="left:0;top:0" width="310" height="432"><polygon points="0,0 310,0 310,360 155,413 0,360" fill="#fff" stroke="#e3e3e6"/><polyline points="0,362 155,415 310,362" fill="none" stroke="#0f1745" stroke-width="4"/><rect x="137" y="386" width="36" height="36" transform="rotate(45 155 404)" fill="#0f1745"/><path d="M155,396 V412 M147,404 H163" stroke="#fff" stroke-width="4"/></svg>
    <div class="shot" role="img" aria-label="Photograph of a trader with a tablet in front of market screens" style="background:linear-gradient(120deg,#e8ebee,#c9ced4 55%,#5c6169)"></div>
    <div class="svc-title">TRADING</div>
    <p class="svc-text">Unde omnis iste natus error sit volupta tem accusantium doloremque lauda ntium, totam aperiaco nsequuntur magnimea.</p>
  </div>
  <div class="svc" style="left:779px">
    <svg class="abs" style="left:0;top:0" width="310" height="432"><polygon points="0,0 310,0 310,360 155,413 0,360" fill="#fff" stroke="#e3e3e6"/><polyline points="0,362 155,415 310,362" fill="none" stroke="#0f1745" stroke-width="4"/><rect x="137" y="386" width="36" height="36" transform="rotate(45 155 404)" fill="#0f1745"/><path d="M155,396 V412 M147,404 H163" stroke="#fff" stroke-width="4"/></svg>
    <div class="shot" role="img" aria-label="Photograph of a twin-engine jet taxiing head-on" style="background:linear-gradient(180deg,#9aa8bd,#c4ccd6 55%,#6d6f70)"></div>
    <div class="svc-title">PROCUREMENT &amp; LEASING</div>
    <p class="svc-text">Unde omnis iste natus error sit volupta tem accusantium doloremque lauda ntium, totam aperiaco nsequuntur magnimea.</p>
  </div>

  <!-- about -->
  <div class="abs about-art" role="img" aria-label="Illustration of a wide-body freighter flying among clouds"></div>
  <div class="abs about-panel"></div>
  <h2 class="abs about-title serif">ABOUT US</h2>
  <p class="abs about-text" style="top:1547px">Founded in 2011, Calder Aviation's management has many years of experience in Aviation, a strong background in scheduled airlines with emphasis in all cargo operations, freight forwarding supply chain and freight logistics, as well as ACMI and CMI operations.</p>
  <p class="abs about-text" style="top:1694px">Calder’s focuses in facilitating wet and dry lease operations, charter and ACMI programs consultancy, aircraft sales, leasing and procurement</p>
  <div class="abs btn-line">LEARN MORE</div>

  <!-- aircraft available -->
  <div class="abs fleet"></div>
  <h2 class="abs fleet-title serif">AIRCRAFT AVAILABLE FOR<br>SALE/LEASE</h2>
  <svg class="abs" style="left:44px;top:2252px" width="20" height="24"><path d="M14,3 L5,12 L14,21" fill="none" stroke="#fff" stroke-width="3"/></svg>
  <svg class="abs" style="left:1134px;top:2252px" width="20" height="24"><path d="M6,3 L15,12 L6,21" fill="none" stroke="#fff" stroke-width="3"/></svg>

  <div class="offer" style="left:112px">
    <svg class="icon" viewBox="0 0 72 72"><rect x="14" y="14" width="44" height="44" transform="rotate(45 36 36)" fill="var(--tile)"/><path d="M25,47 H48 M28,44 V38 M33,44 V34 M38,44 V36 M43,44 V29 M27,35 L34,29 L39,32 L46,25" fill="none" stroke="#111a4d" stroke-width="3"/></svg>
    <div class="offer-title">SALE/LEASEBACK</div>
    <p class="offer-text">Sale-leaseback is a method of financing. If your company needs liquidity</p>
    <div class="more">READ MORE &nbsp;»</div>
  </div>
  <div class="offer" style="left:360px">
    <svg class="icon" viewBox="0 0 72 72"><rect x="14" y="14" width="44" height="44" transform="rotate(45 36 36)" fill="var(--tile)"/><rect x="27" y="24" width="16" height="22" fill="none" stroke="#111a4d" stroke-width="2.2"/><path d="M30,30 H40 M30,34 H40 M30,38 H40 M46,26 V44" stroke="#111a4d" stroke-width="2"/></svg>
    <div class="offer-title">DRY LEASE</div>
    <p class="offer-text">We offer aircraft from our own portfolio on dry lease or could engage in procuring</p>
    <div class="more">READ MORE &nbsp;»</div>
  </div>
  <div class="offer" style="left:608px">
    <svg class="icon" viewBox="0 0 72 72"><rect x="14" y="14" width="44" height="44" transform="rotate(45 36 36)" fill="var(--tile)"/><circle cx="35" cy="35" r="10" fill="none" stroke="#111a4d" stroke-width="2"/><ellipse cx="35" cy="35" rx="4.5" ry="10" fill="none" stroke="#111a4d" stroke-width="1.6"/><path d="M25,35 H45 M27,30 H43 M27,40 H43" stroke="#111a4d" stroke-width="1.5"/><circle cx="44" cy="44" r="3.5" fill="none" stroke="#111a4d" stroke-width="1.8"/></svg>
    <div class="offer-title">WORLDWIDE CHARTERS</div>
    <p class="offer-text">We facilitate the arrangement of full charters to airlines and logistics companies.</p>
    <div class="more">READ MORE &nbsp;»</div>
  </div>
  <div class="offer" style="left:857px">
    <svg class="icon" viewBox="0 0 72 72"><rect x="14" y="14" width="44" height="44" transform="rotate(45 36 36)" fill="var(--tile)"/><rect x="27" y="27" width="18" height="18" rx="2" fill="none" stroke="#111a4d" stroke-width="2.2"/><path d="M32,27 V24 H40 V27 M27,35 H45" fill="none" stroke="#111a4d" stroke-width="2"/></svg>
    <div class="offer-title">AVIATION CONSULTANCY</div>
    <p class="offer-text">We provide airline consultancy services for new or special projects.</p>
    <div class="more">READ MORE &nbsp;»</div>
  </div>

  <!-- blog -->
  <h2 class="section" style="top:2582px">LATEST BLOG</h2>
  <div class="post-img" style="left:112px;background:linear-gradient(160deg,#8c9094,#b7b9b8 50%,#6e7272)" role="img" aria-label="Aerial photograph of a jumbo jet parked at a terminal"></div>
  <div class="post-img" style="left:445px;background:linear-gradient(180deg,#dfe3e8,#8a96a3 45%,#c68a48 85%,#3b3f47)" role="img" aria-label="Photograph of a jet flying between skyscrapers at sunset"></div>
  <div class="post-img" style="left:779px;background:linear-gradient(180deg,#6e9fd3,#a9c4d8 55%,#e8c46a 100%)" role="img" aria-label="Illustration of a jet above clouds at sunrise"></div>

  <div class="post" style="left:121px">
    <div class="post-date"><svg width="13" height="13" viewBox="0 0 13 13" style="vertical-align:-1px;margin-right:8px"><rect x="1" y="2" width="11" height="10" fill="none" stroke="#333" stroke-width="1.5"/><path d="M1,5 H12 M4,0 V3 M9,0 V3" stroke="#333" stroke-width="1.5"/></svg>18 DEC 2021</div>
    <div class="post-title">SED UT PERSPICIATIS UNDEA</div>
    <p class="post-text">Lorem ipsum dolor sit amet, consec te tur adipi scing do eiusmodea.</p>
    <div class="more">READ MORE &nbsp;»</div>
  </div>
  <div class="post" style="left:454px">
    <div class="post-date"><svg width="13" height="13" viewBox="0 0 13 13" style="vertical-align:-1px;margin-right:8px"><rect x="1" y="2" width="11" height="10" fill="none" stroke="#333" stroke-width="1.5"/><path d="M1,5 H12 M4,0 V3 M9,0 V3" stroke="#333" stroke-width="1.5"/></svg>18 DEC 2021</div>
    <div class="post-title">SED UT PERSPICIATIS UNDEA</div>
    <p class="post-text">Lorem ipsum dolor sit amet, consec te tur adipi scing do eiusmodea.</p>
    <div class="more">READ MORE &nbsp;»</div>
  </div>
  <div class="post" style="left:788px">
    <div class="post-date"><svg width="13" height="13" viewBox="0 0 13 13" style="vertical-align:-1px;margin-right:8px"><rect x="1" y="2" width="11" height="10" fill="none" stroke="#333" stroke-width="1.5"/><path d="M1,5 H12 M4,0 V3 M9,0 V3" stroke="#333" stroke-width="1.5"/></svg>18 DEC 2021</div>
    <div class="post-title">SED UT PERSPICIATIS UNDEA</div>
    <p class="post-text">Lorem ipsum dolor sit amet, consec te tur adipi scing do eiusmodea.</p>
    <div class="more">READ MORE &nbsp;»</div>
  </div>

  <!-- footer -->
  <svg class="abs" style="left:0;top:3090px" width="1200" height="462" viewBox="0 0 1200 462">
    <polygon points="0,4 600,136 1200,4 1200,462 0,462" fill="#0b1233"/>
    <polygon points="0,4 600,136 1200,4 1200,26 600,160 0,26" fill="#121b4a"/>
    <g transform="translate(600,152)">
      <rect x="-17" y="-17" width="34" height="34" transform="rotate(45)" fill="#121b4a"/>
      <path d="M0,-16 L3,-3 L16,0 L3,3 L0,16 L-3,3 L-16,0 L-3,-3 Z" fill="#ffffff"/>
    </g>
  </svg>
  <div class="abs foot-brand">CALDER<br>AVIATION</div>
  <div class="abs social" style="left:168px"></div>
  <div class="abs social" style="left:202px"></div>
  <div class="abs social" style="left:236px"></div>
  <div class="abs social" style="left:270px"></div>

  <div class="foot-col">
    <h4 style="left:436px;top:3305px">Quick Links</h4>
    <ul class="foot-list" style="left:436px;top:3348px"><li>Home</li><li>About Us</li><li>Services</li><li>Projects</li><li>Contact Us</li></ul>
    <h4 style="left:645px;top:3305px">Other Links</h4>
    <ul class="foot-list" style="left:645px;top:3348px"><li>Blog</li><li>Privacy Policy</li><li>Terms Of Use</li><li>Legal Support</li></ul>
    <h4 style="left:859px;top:3305px">Contact Us</h4>
  </div>
  <div class="contact-row" style="top:3350px">
    <svg width="12" height="14" viewBox="0 0 12 14"><path d="M6,14 C2,9 1,7 1,5 A5,5 0 0 1 11,5 C11,7 10,9 6,14 Z" fill="#fff"/><circle cx="6" cy="5" r="2" fill="#0b1233"/></svg>
    <span>465, Lorum Ipsum Dol,<br>United States</span>
  </div>
  <div class="contact-row" style="top:3404px">
    <svg width="13" height="13" viewBox="0 0 13 13"><path d="M2,1 L5,1 L6,4 L4.5,5.5 C5.5,7.5 6,8 7.5,8.5 L9,7 L12,8 L12,11 C12,12 11,12.5 10,12.5 C5,12 1,8 0.5,3 C0.5,2 1,1 2,1 Z" fill="#fff"/></svg>
    <span>(888) 888 8888</span>
  </div>
  <div class="contact-row" style="top:3432px">
    <svg width="14" height="12" viewBox="0 0 14 12"><rect x="1" y="1" width="12" height="10" fill="none" stroke="#fff" stroke-width="1.5"/><path d="M1,1 L7,6 L13,1" fill="none" stroke="#fff" stroke-width="1.5"/></svg>
    <span>info@calderaviation.com</span>
  </div>
  <div class="abs rule"></div>
  <div class="abs copy">© 2021 <b style="color:#fff">CALDER AVIATION</b>. All Rights Reserved</div>

</div>
</body>
</html>
```